Unique Business Card Design

Unique Business Card design for our orthotic and prosthetic company. Our logo is on our website, color is light blue. Unique shape (artificial leg shaped, vertical, etc..) preferred. Logo, business name, individual name and basic demographics needed.

Industry/Entity Type

Business

Contact Information for Business Card

Logo, Industry, Phone # Logo, "Prosthetic & Orthotic Services" Place to add individual name and contact info

Colors
cee9f5

Requirements
Must have
• The icon must be there, placement of "Prosthetic & Orthotic Services" can be moved
Nice to have
• Like the mix of light blue, and a little darker blue. One design included the icons from my website which was a nice touch

```html
<!DOCTYPE html>
<html lang="en">
<head>
<meta charset="utf-8">
<title>LimbWorks Inc. – Business Card</title>
<link rel="stylesheet" href="https://fonts.googleapis.com/css2?family=Roboto:ital,wght@0,400;0,500;0,700;1,400&display=swap">
<style>
  :root {
    --brand-blue: #236399;
    --band-dark: #343b42;
    --card-white: #f5f5f5;
    --text-dark: #333333;
    --stage: #ebebeb;
    --on-blue: #ffffff;
  }
  * { margin: 0; padding: 0; box-sizing: border-box; }
  html, body { width: 1200px; height: 576px; overflow: hidden; }
  body {
    background: var(--stage);
    font-family: "Roboto", Arial, sans-serif;
    position: relative;
  }
  .card {
    position: absolute;
    border-radius: 6px;
    overflow: hidden;
  }

  /* Front */
  .card-front {
    left: 82px; top: 139px; width: 484px; height: 291px;
    background: var(--brand-blue);
    color: var(--on-blue);
  }
  .front-mark {
    position: absolute; left: 92px; top: 107px;
    width: 78px; height: 78px; border-radius: 50%;
    background: var(--on-blue);
  }
  .front-name {
    position: absolute; left: 190px; top: 108px;
    font-size: 22px; font-weight: 700; letter-spacing: 0.3px;
  }
  .front-tagline {
    position: absolute; left: 204px; top: 142px;
    font-size: 12.5px; font-weight: 400;
  }
  .front-phone {
    position: absolute; left: 213px; top: 159px;
    font-size: 21px; font-weight: 700; letter-spacing: 1px;
  }

  /* Back */
  .card-back {
    left: 602px; top: 138px; width: 480px; height: 290px;
    background: var(--card-white);
    color: var(--text-dark);
  }
  .side-band {
    position: absolute; left: 0; top: 0; bottom: 0; width: 40px;
    background: var(--brand-blue);
    border-right: 6px solid var(--band-dark);
    width: 46px;
  }
  .back-mark {
    position: absolute; left: 218px; top: 25px;
    width: 60px; height: 60px; border-radius: 50%;
    background: var(--brand-blue);
  }
  .back-name {
    position: absolute; left: 293px; top: 33px;
    font-size: 17.5px; font-weight: 700; color: var(--brand-blue);
    letter-spacing: 0.2px;
  }
  .back-tagline {
    position: absolute; left: 304px; top: 58px;
    font-size: 9.5px; color: var(--brand-blue);
  }
  .person-name {
    position: absolute; left: 67px; top: 116px;
    font-size: 19px; font-weight: 700; color: var(--brand-blue);
  }
  .person-title {
    position: absolute; left: 67px; top: 141px;
    font-size: 11.5px; font-style: italic;
  }
  .contact {
    position: absolute;
    display: flex; align-items: center; gap: 8px;
    font-size: 13px;
  }
  .contact svg { width: 12px; height: 12px; fill: var(--brand-blue); flex: none; }
  .mobile { left: 67px; top: 160px; font-size: 14px; }
  .office { left: 67px; top: 213px; }
  .fax { left: 67px; top: 231px; }
  .web { left: 195px; top: 213px; }
  .mail { left: 195px; top: 231px; }
  .address { position: absolute; left: 67px; top: 251px; font-size: 13px; }
</style>
</head>
<body>

<section class="card card-front" aria-label="Card front">
  <div class="front-mark" aria-hidden="true"></div>
  <div class="front-name">LIMBWORKS INC.</div>
  <div class="front-tagline">Prosthetic &amp; Orthotic Services</div>
  <div class="front-phone">555.210.4400</div>
</section>

<section class="card card-back" aria-label="Card back">
  <div class="side-band"></div>
  <div class="back-mark" aria-hidden="true"></div>
  <div class="back-name">LIMBWORKS INC.</div>
  <div class="back-tagline">Prosthetic &amp; Orthotic Services</div>

  <div class="person-name">Mara Ellison</div>
  <div class="person-title">Orthotist/Prosthetist</div>

  <div class="contact mobile">
    <svg viewBox="0 0 12 12"><rect x="2.5" y="0" width="7" height="12" rx="1.2"/><rect x="3.8" y="1.5" width="4.4" height="7.5" fill="#f5f5f5"/></svg>
    <span>555-3081927</span>
  </div>
  <div class="contact office">
    <svg viewBox="0 0 12 12"><path d="M0 4 Q6 0 12 4 L12 5.5 L9 5.5 L9 4 L3 4 L3 5.5 L0 5.5 Z"/><rect x="1.5" y="6" width="9" height="5.5" rx="1"/></svg>
    <span>555.210.4400</span>
  </div>
  <div class="contact fax">
    <svg viewBox="0 0 12 12"><rect x="3" y="0.5" width="6" height="3.5"/><rect x="0.5" y="4" width="11" height="5" rx="1"/><rect x="3" y="7.5" width="6" height="4"/></svg>
    <span>555.210.4419</span>
  </div>
  <div class="contact web">
    <svg viewBox="0 0 12 12"><circle cx="6" cy="6" r="5.5"/><path d="M0.5 6 H11.5 M6 0.5 V11.5 M6 0.5 Q2.5 6 6 11.5 M6 0.5 Q9.5 6 6 11.5" stroke="#f5f5f5" stroke-width="0.8" fill="none"/></svg>
    <span>www.limbworksinc.com</span>
  </div>
  <div class="contact mail">
    <svg viewBox="0 0 12 12"><rect x="0" y="2" width="12" height="8" rx="0.6"/><path d="M0.5 2.5 L6 6.5 L11.5 2.5" stroke="#f5f5f5" stroke-width="0.9" fill="none"/></svg>
    <span>mellison@limbworksinc.com</span>
  </div>
  <div class="address">820 Harbor Ave. Easton, MD 21601</div>
</section>

</body>
</html>
```